Corvel Capital LLC

Need Professional Business cards for New Investment Fund

Target Market(s)

High Quality investors

Industry/Entity Type

Financial

Contact Information for Business Card

Phone Number +1 555 284 6190
Name Lukas Varenko
Title Fund Manager
email lv@FundCorvel.com
Website www.FundCorvel.com

Colors

Designer to choose colors to be used in the design.

Requirements
Must have
• Must have our Logo and all of the above. Must be made so lettering and loge can be raised

```html
<!DOCTYPE html>
<html lang="en">
<head>
<meta charset="utf-8">
<title>Business Card – Fund Manager</title>
<link href="https://fonts.googleapis.com/css2?family=Roboto:wght@400;500;700&display=swap" rel="stylesheet">
<style>
  :root {
    --backdrop: #d9d9d9;
    --forest-top: #545e52;
    --forest-bottom: #434c40;
    --signal-green: #2fe312;
    --paper: #ffffff;
    --ink-forest: #4a5446;
  }
  * { box-sizing: border-box; margin: 0; padding: 0; }
  html, body {
    width: 1200px; height: 1200px; overflow: hidden;
    background: var(--backdrop);
    font-family: "Roboto", Arial, sans-serif;
  }
  .card {
    position: absolute; left: 257px;
    width: 686px; height: 392px;
    overflow: hidden;
    box-shadow: 0 14px 28px rgba(0,0,0,0.18);
  }
  .card--front { top: 165px; background: var(--paper); }
  .card--back {
    top: 653px;
    background: linear-gradient(var(--forest-top), var(--forest-bottom));
  }
  .front__contact {
    position: absolute; left: 0; top: 0;
    width: 309px; height: 100%;
    background: linear-gradient(var(--forest-top), var(--forest-bottom));
  }
  .growth-line { position: absolute; left: 309px; top: 0; width: 20px; height: 100%; }
  .holder-name {
    position: absolute; left: 32px; top: 125px;
    font-size: 24px; font-weight: 700; color: var(--signal-green);
    white-space: nowrap;
  }
  .holder-title {
    position: absolute; left: 32px; top: 156px;
    font-size: 15.5px; font-weight: 500; color: var(--paper);
  }
  .contact-list {
    position: absolute; left: 32px; top: 201px;
    list-style: none;
  }
  .contact-list li {
    display: flex; align-items: center;
    height: 19.5px;
    font-size: 15.5px; color: var(--paper);
    white-space: nowrap;
  }
  .contact-list svg { width: 13px; height: 13px; margin-right: 10px; flex: none; }
  .brand {
    position: absolute; display: flex; align-items: center; gap: 10px;
    font-weight: 500; letter-spacing: 1px; white-space: nowrap;
  }
  .brand__dot { border-radius: 50%; flex: none; }
  .brand--front { left: 329px; right: 0; justify-content: center; top: 172px; font-size: 40px; color: var(--ink-forest); }
  .brand--front .brand__dot { width: 18px; height: 18px; background: var(--signal-green); }
  .brand--back { left: 0; right: 0; justify-content: center; top: 164px; font-size: 48px; color: var(--paper); }
  .brand--back .brand__dot { width: 20px; height: 20px; background: var(--paper); }
  .back__url {
    position: absolute; left: 0; right: 0; top: 347px;
    text-align: center; font-size: 15.5px; letter-spacing: 3.6px;
    color: var(--paper);
  }
</style>
</head>
<body>
  <section class="card card--front">
    <div class="front__contact">
      <p class="holder-name">Lukas Varenko</p>
      <p class="holder-title">Fund Manager</p>
      <ul class="contact-list">
        <li>
          <svg viewBox="0 0 16 16" aria-hidden="true"><path fill="#2fe312" d="M3.5 1.5l2.5 0 1.2 3.2-1.6 1.2c.8 1.8 2.2 3.2 4 4l1.2-1.6 3.2 1.2v2.5c0 .8-.7 1.5-1.5 1.5C7 13.5 2.5 9 2 3c0-.8.7-1.5 1.5-1.5z"/></svg>
          +1 555 284 6190
        </li>
        <li>
          <svg viewBox="0 0 16 16" aria-hidden="true"><rect x="1" y="4" width="14" height="9" fill="#2fe312"/><path d="M1.5 4.5L8 9l6.5-4.5" fill="none" stroke="#4a5446" stroke-width="1.2"/></svg>
          lv@FundCorvel.com
        </li>
        <li>
          <svg viewBox="0 0 16 16" aria-hidden="true"><circle cx="8" cy="8" r="6.5" fill="#2fe312"/><path d="M5 4.5c1.5.5 1.5 2 3 2.5s.5 2-1 2.5M10 10.5c.5-1 1.5-1 2-.5" fill="none" stroke="#4a5446" stroke-width="1.3"/></svg>
          www.FundCorvel.com
        </li>
      </ul>
    </div>
    <svg class="growth-line" viewBox="0 0 20 392" aria-hidden="true">
      <rect x="1" y="26" width="5" height="366" fill="#2fe312"/>
      <polygon points="1,16 1,42 17,42" fill="#2fe312"/>
    </svg>
    <div class="brand brand--front"><span class="brand__dot"></span>Tarnwick</div>
  </section>

  <section class="card card--back">
    <div class="brand brand--back"><span class="brand__dot"></span>Tarnwick</div>
    <p class="back__url">www.FundCorvel.com</p>
  </section>
</body>
</html>
```